Wedding Invitation for a wedding at home - personal, romantic event

Want a wedding invitation that is to be printed onto card.
Size to be 148mm x 210mm
For it to open like a book not tent card
Have a picture of a house that I want to be the front cover.
I've attached 2 pictures. I like the picture without the man but with the grass
For the photo to become a drawing and the colours to be brighter.
If you could use the picture of us and get us in one of the windows.
If you could put the picture of the dog maybe somewhere on the grass.
Love the colour of the sky in the picture of the beach

Words to be on the inside of the card:
Together with our families
You are invited to the Wedding Reception of Tessa Pimble and Roy Fenwick
On Saturday 9th of September 2017 at 6pm
At Fenwick's Keep, 41b, Marrow Crescent, Camberley, Surrey, RH19 4PW
Carriages at 1am
RSVP by Friday 27th of July to 07713 586 201

Words on the Back page:
With all that we have, we've been truly blessed.
Your presence and prayers are all that we request.
But if you desire to give nonetheless,
Monetary gift is one we suggest.

If the pages can be white.
Writing in gold
gold border on all pages

Target Market(s)

Wedding guests

Industry/Entity Type

Wedding

Font styles to use
Script

Requirements
Must have
• Romantic feel. Our wedding colours are white, gold and rose gold.
• Designer to be creative and I do not have much inspiration.
Nice to have
• metallic colours
• Maybe have MR & MRS in gold metallic on the front page

```html
<!DOCTYPE html>
<html lang="en">
<head>
<meta charset="utf-8">
<title>Wedding Reception Invitation – Tessa Pimble &amp; Roy Fenwick</title>
<link rel="stylesheet" href="https://fonts.googleapis.com/css2?family=EB+Garamond:wght@400&family=Great+Vibes&display=swap">
<style>
  :root {
    --paper: #ffffff;
    --gold: #928b2c;
  }
  html, body {
    margin: 0;
    padding: 0;
    overflow: hidden;
    background: var(--paper);
  }
  .invitation {
    position: relative;
    width: 846px;
    height: 1200px;
    background: var(--paper);
    color: var(--gold);
    font-family: "EB Garamond", "Times New Roman", serif;
    overflow: hidden;
  }
  .line {
    position: absolute;
    left: 0;
    right: 0;
    text-align: center;
    text-transform: uppercase;
    font-size: 22px;
    letter-spacing: 1.2px;
    line-height: 32px;
    white-space: nowrap;
  }
  .name {
    position: absolute;
    left: 0;
    right: 0;
    text-align: center;
    font-family: "Great Vibes", cursive;
    font-size: 76px;
    line-height: 100px;
    white-space: nowrap;
  }
</style>
</head>
<body>
  <main class="invitation">
    <div class="line intro" style="top:205px">Together with our families</div>
    <div class="name bride" style="top:256px">Tessa Pimble</div>
    <div class="line conjunction" style="top:374px">and</div>
    <div class="name groom" style="top:422px">Roy Fenwick</div>

    <div class="line invite" style="top:560px">Invite you to their</div>
    <div class="line invite" style="top:593px">wedding reception</div>

    <div class="line date" style="top:657px">On Saturday 9th of September 2017</div>
    <div class="line time" style="top:689px">at 6pm</div>

    <div class="line venue" style="top:754px">At Fenwick’s Keep</div>
    <div class="line address" style="top:786px">41b, Marrow Crescent, Camberley</div>
    <div class="line address" style="top:819px">Surrey, RH19 4PW</div>

    <div class="line carriages" style="top:884px">Carriages at 1am</div>

    <div class="line rsvp" style="top:1013px">RSVP by Friday 27th of July</div>
    <div class="line rsvp" style="top:1048px">to 07713 586 201</div>
  </main>
</body>
</html>
```